Business Card Design for a Personal Trainer

I need a business card design for my job as a personal trainer. It should have a unique, modern and exclusive design. On the front there should be only my logo with my name and my job. 0162/3819204 Tobias Lendhart Wiesengrundweg 14 80417 Munich Germany The most important contact information is the web adress. it can be bigger than the rest, but its not necessary. The card should be 8,5cmx5,5cm big. Font: Roboto. Colors: black, white, gray, 56c1ff.

```html
<!DOCTYPE html>
<html lang="de">
<head>
<meta charset="utf-8">
<title>Tobias Lendhart – Personal Trainer</title>
<link href="https://fonts.googleapis.com/css2?family=Roboto:wght@300;400&display=swap" rel="stylesheet">
<style>
  :root {
    --page-bg: #e6e4e1;
    --card-dark: #070707;
    --card-mid: #1c1c1c;
    --card-edge: #bdbdbd;
    --text-light: #d6d6d6;
    --text-soft: #b4b4b4;
    --rule: #9a9a9a;
    --photo-top: #3a3a3a;
    --photo-bottom: #141414;
  }
  html, body {
    margin: 0;
    padding: 0;
    width: 1200px;
    height: 970px;
    overflow: hidden;
    background: var(--page-bg);
    font-family: "Roboto", sans-serif;
  }
  .card {
    position: absolute;
    left: 100px;
    top: 209px;
    width: 1000px;
    height: 552px;
    box-sizing: border-box;
    border: 2px solid var(--card-edge);
    border-radius: 4px;
    background: radial-gradient(ellipse 55% 75% at 22% 45%, var(--card-mid) 0%, var(--card-dark) 70%);
    overflow: hidden;
    color: var(--text-light);
  }
  .portrait {
    position: absolute;
    left: 54px;
    top: 70px;
    width: 345px;
    height: 482px;
    background: linear-gradient(180deg, var(--photo-top) 0%, var(--photo-bottom) 100%);
    border-radius: 150px 150px 0 0;
  }
  .brand {
    position: absolute;
    left: 449px;
    top: 178px;
    width: 400px;
    text-align: center;
  }
  .brand-name {
    font-weight: 300;
    font-size: 40px;
    line-height: 48px;
    letter-spacing: 1px;
    color: var(--text-light);
    white-space: nowrap;
  }
  .brand-role {
    display: flex;
    align-items: center;
    gap: 8px;
    margin-top: 2px;
    font-weight: 300;
    font-size: 15px;
    letter-spacing: 4px;
    color: var(--text-soft);
  }
  .brand-role::before,
  .brand-role::after {
    content: "";
    flex: 1;
    height: 1px;
    background: var(--rule);
  }
  .contact {
    position: absolute;
    left: 535px;
    top: 264px;
  }
  .contact-name {
    font-size: 28px;
    line-height: 36px;
    color: var(--text-light);
    margin: 0 0 14px;
  }
  .address {
    font-style: normal;
    font-weight: 300;
    font-size: 22px;
    line-height: 27px;
    color: var(--text-soft);
    margin: 0 0 20px;
  }
  .contact-line {
    display: flex;
    align-items: center;
    gap: 10px;
    font-weight: 300;
    font-size: 22px;
    line-height: 34px;
    color: var(--text-soft);
  }
  .contact-line svg {
    width: 20px;
    height: 20px;
    fill: none;
    stroke: var(--text-soft);
    stroke-width: 1.6;
  }
  .website {
    position: absolute;
    left: 451px;
    top: 478px;
    font-weight: 300;
    font-size: 33px;
    line-height: 40px;
    letter-spacing: 0.5px;
    color: var(--text-light);
  }
</style>
</head>
<body>
  <div class="card">
    <div class="portrait" role="img" aria-label="Portrait of the trainer with arms crossed, black and white"></div>

    <div class="brand">
      <div class="brand-name">TOBIAS LENDHART</div>
      <div class="brand-role">PERSONAL TRAINER</div>
    </div>

    <div class="contact">
      <p class="contact-name">Tobias Lendhart</p>
      <p class="address">Wiesengrundweg 14<br>80417 München</p>
      <div class="contact-line">
        <svg viewBox="0 0 20 20" aria-hidden="true">
          <path d="M5 2.5 L8 6 L6.5 8.5 Q8 12 11.5 13.5 L14 12 L17.5 15 L15.5 17.5 Q9 18 5 13 Q1.5 8 2.5 4.5 Z"/>
        </svg>
        <span>0162/3819204</span>
      </div>
      <div class="contact-line">
        <svg viewBox="0 0 20 20" aria-hidden="true">
          <rect x="2" y="4.5" width="16" height="11"/>
          <path d="M2 4.5 L10 11 L18 4.5"/>
        </svg>
        <span>t.lendhart@mailpost.de</span>
      </div>
    </div>

    <div class="website">www.lendhart-training.de</div>
  </div>
</body>
</html>
```